Mira Bloom Fitness Coaching Project

I am a personal trainer based in London. My services include one-on-one PT sessions, bootcamps.
I would like the design to be minimalistic. With light colours: white, pink, purple.
I specialise in weight loss, flexibility, mobility.

Tessa Brogan
Personal Trainer
Email: tessa.brogan@quellmail.com
tel: 07700218493
Instagram: Mira Bloom

Target Market(s)

adults, mostly females (age 18-50).

Industry/Entity Type

Fitness

Contact Information for Business Card

Tessa Brogan
Personal Trainer
tel: 07700218493
Instagram: Mira Bloom

Font styles to use
Serif

Colors
eea4c8
fbd4d5
fdf9cf
cfeae6
cee9f5

Requirements
Nice to have
• minimalistic style
• easy to read and remember

```html
<!DOCTYPE html>
<html lang="en">
<head>
<meta charset="utf-8">
<title>Tessa Brogan – Business Card</title>
<link href="https://fonts.googleapis.com/css2?family=Jost:wght@400;500&display=swap" rel="stylesheet">
<style>
  :root {
    --page: #ececec;
    --ink-black: #050505;
    --mint: #cfeae6;
    --white: #ffffff;
    --paper: #fdfdfd;
    --pink: #eca3c9;
    --pink-line: #f0b3d2;
  }
  * { margin: 0; padding: 0; box-sizing: border-box; }
  html, body {
    width: 1200px; height: 859px; overflow: hidden;
    background: var(--page);
    font-family: "Jost", "Futura", sans-serif;
  }
  .sheet {
    position: relative; width: 1200px; height: 859px;
    display: flex; align-items: center; justify-content: center; gap: 40px;
  }
  .card {
    position: relative; width: 540px; height: 309px;
    box-shadow: 0 8px 24px rgba(0,0,0,0.12);
  }
  .card--back {
    background: var(--ink-black);
    border: 9px solid var(--mint);
    display: flex; align-items: center; justify-content: center;
  }
  .back-name {
    color: var(--white); font-weight: 400; font-size: 30px;
    letter-spacing: 0.28em; padding-left: 0.28em;
  }
  .card--front { background: var(--paper); color: var(--pink); }
  .front-name {
    position: absolute; top: 34px; right: 34px;
    font-size: 28px; font-weight: 400; letter-spacing: 0.24em;
  }
  .rule-long {
    position: absolute; left: 40px; right: 34px; top: 198px;
    height: 1px; background: var(--pink-line);
  }
  .social {
    position: absolute; right: 36px; top: 170px;
    display: flex; align-items: center; gap: 8px;
    font-size: 13px; letter-spacing: 0.18em;
  }
  .social-mark {
    width: 10px; height: 10px; background: var(--pink); border-radius: 2px;
  }
  .identity { position: absolute; left: 40px; top: 150px; }
  .identity-name { font-size: 22px; font-weight: 500; letter-spacing: 0.2em; line-height: 1.1; }
  .identity-role { font-size: 12px; letter-spacing: 0.2em; margin-top: 2px; }
  .rule-short {
    position: absolute; left: 40px; top: 232px; width: 190px;
    height: 1px; background: var(--pink-line);
  }
  .contacts { position: absolute; left: 40px; top: 244px; font-size: 13px; letter-spacing: 0.14em; }
  .contact { display: flex; align-items: center; gap: 9px; line-height: 1.6; }
  .contact svg { width: 11px; height: 11px; flex: none; }
</style>
</head>
<body>
<main class="sheet">
  <section class="card card--back">
    <h1 class="back-name">TESSA BROGAN</h1>
  </section>

  <section class="card card--front">
    <h2 class="front-name">TESSA BROGAN</h2>

    <div class="identity">
      <p class="identity-name">Tessa Brogan</p>
      <p class="identity-role">Personal Trainer</p>
    </div>

    <div class="rule-long"></div>

    <div class="social">
      <span class="social-mark"></span>
      <span>Mira Bloom</span>
    </div>

    <div class="rule-short"></div>

    <div class="contacts">
      <p class="contact">
        <svg viewBox="0 0 24 24" aria-hidden="true"><path fill="#eca3c9" d="M6.6 10.8a15.1 15.1 0 0 0 6.6 6.6l2.2-2.2c.3-.3.7-.4 1-.2 1.1.4 2.3.6 3.6.6.6 0 1 .4 1 1V20c0 .6-.4 1-1 1A17 17 0 0 1 3 4c0-.6.4-1 1-1h3.5c.6 0 1 .4 1 1 0 1.3.2 2.5.6 3.6.1.3 0 .7-.2 1z"/></svg>
        <span>07700218493</span>
      </p>
      <p class="contact">
        <svg viewBox="0 0 24 24" aria-hidden="true"><rect x="2.5" y="5" width="19" height="14" rx="1.5" fill="none" stroke="#eca3c9" stroke-width="2"/><path d="M3 6l9 7 9-7" fill="none" stroke="#eca3c9" stroke-width="2"/></svg>
        <span>tessa.brogan@quellmail.com</span>
      </p>
    </div>
  </section>
</main>
</body>
</html>
```